High-end construction company needs a business card design

We need a modern looking business card that draws people in, is memorable and looks so good people will want to sick it on their fridges.
On the first side what is needed are:
Logo
My name - Tomasz Brelwik
Title - Managing Director
Website - www.varkelt.co.uk
Email - tomasz@varkelt.co.uk
Telephone - 020 5194 6281
Mobile - 07845139072
On the back side was is needed is a list of all the services we provide:
-Kitchen Renovations
-Bathroom Renovations
-House Renovations
-Garage Conversions
-Extensions
-Loft Conversions
-Conservatories
-Carpentry
-Tiling
-Electrical
-Plumbing & Heating
-Bricklaying
-Landscaping
-Decorating
-Plastering
We would like the colours to be the same shades as on the logo with grey or black for the words.
Target Market(s)
Anyone who needs building work done
Contact Information for Business Card
This business card is for a construction company which strives to deliver excellent service and quality.
The look and feel of the card should represent this.
Requirements
Must have
- On the first side what is needed are:
Logo
My name - Tomasz Brelwik
Title - Managing Director
Website - www.varkelt.co.uk
Email - tomasz@varkelt.co.uk
Telephone - 020 5194 6281
Mobile - 07845139072
Nice to have
- Cool looking features

```html
<!DOCTYPE html>
<html lang="en">
<head>
<meta charset="utf-8">
<title>Varkelt Construction Ltd – Business Card</title>
<link rel="stylesheet" href="https://fonts.googleapis.com/css2?family=Lato:wght@400;700;900&display=swap">
<style>
  :root {
    --green: #5bb832;
    --green-dark: #3f9a2a;
    --ink: #3c3c3c;
    --paper: #ffffff;
    --backdrop: #3a3431;
  }
  * { margin: 0; padding: 0; box-sizing: border-box; }
  html, body { width: 1200px; height: 847px; overflow: hidden; }
  body {
    background: var(--backdrop);
    font-family: "Lato", sans-serif;
    display: flex;
    align-items: center;
    justify-content: center;
    gap: 40px;
  }
  .card {
    width: 540px;
    height: 309px;
    background: var(--paper);
    border-bottom: 6px solid var(--green);
    position: relative;
    box-shadow: 0 10px 24px rgba(0,0,0,0.35);
  }
  .brand {
    color: var(--green);
    font-weight: 900;
    text-align: center;
    line-height: 1;
  }
  .brand-mark {
    display: inline-block;
    width: 14px; height: 14px;
    background: var(--green);
    margin-right: 8px;
    vertical-align: middle;
  }
  .brand-name { font-size: 40px; letter-spacing: 1px; vertical-align: middle; }
  .brand-sub { font-size: 13px; letter-spacing: 3px; margin-top: 6px; text-transform: uppercase; }

  /* Services side */
  .card--services .brand { padding-top: 56px; }
  .services {
    list-style: none;
    margin-top: 30px;
    text-align: center;
    color: var(--ink);
    font-size: 14px;
    line-height: 1.55;
  }
  .services .sep { color: var(--green); margin: 0 5px; }

  /* Contact side */
  .card--contact { display: flex; align-items: center; }
  .card--contact .brand { width: 270px; }
  .divider {
    width: 1px; height: 150px;
    background: var(--green);
  }
  .person { padding-left: 30px; }
  .person-name { color: var(--green-dark); font-weight: 700; font-size: 26px; }
  .person-title { color: var(--ink); font-size: 15px; margin-top: 2px; }
  .contacts { list-style: none; margin-top: 14px; color: var(--ink); font-size: 15px; }
  .contacts li { display: flex; align-items: center; gap: 10px; line-height: 1.45; }
  .contacts svg { width: 14px; height: 14px; flex: none; }
  .contacts .accent { color: var(--green); }
</style>
</head>
<body>
  <section class="card card--services">
    <div class="brand">
      <span class="brand-mark"></span><span class="brand-name">VARKELT</span>
      <div class="brand-sub">Construction Ltd</div>
    </div>
    <ul class="services">
      <li>Kitchen Renovations<span class="sep">/</span>Bathroom Renovations<span class="sep">/</span>House Renovations</li>
      <li>Garage Conversions<span class="sep">/</span>Extensions<span class="sep">/</span>Loft Conversions<span class="sep">/</span>Conservatories</li>
      <li>Carpentry<span class="sep">/</span>Tiling<span class="sep">/</span>Electrical<span class="sep">/</span>Plumbing &amp; Heating</li>
      <li>Bricklaying<span class="sep">/</span>Landscaping<span class="sep">/</span>Decorating<span class="sep">/</span>Plastering</li>
    </ul>
  </section>

  <section class="card card--contact">
    <div class="brand">
      <span class="brand-mark"></span><span class="brand-name">VARKELT</span>
      <div class="brand-sub">Construction Ltd</div>
    </div>
    <div class="divider"></div>
    <div class="person">
      <div class="person-name">Tomasz Brelwik</div>
      <div class="person-title">Managing Director</div>
      <ul class="contacts">
        <li><svg viewBox="0 0 16 16"><path fill="var(--green)" d="M3 2h3l1 3-2 1.5a9 9 0 0 0 4.5 4.5L11 9l3 1v3a1 1 0 0 1-1 1A11 11 0 0 1 2 3a1 1 0 0 1 1-1z"/></svg>020 5194 6281</li>
        <li><svg viewBox="0 0 16 16"><rect x="4" y="1" width="8" height="14" rx="1.5" fill="none" stroke="var(--green)" stroke-width="1.6"/><circle cx="8" cy="12.3" r="0.9" fill="var(--green)"/></svg>07845139072</li>
        <li><svg viewBox="0 0 16 16"><rect x="1" y="3" width="14" height="10" fill="var(--green)"/><path d="M1 3l7 6 7-6" fill="none" stroke="#fff" stroke-width="1.3"/></svg>tomasz@varkelt.co.uk</li>
        <li><svg viewBox="0 0 16 16"><circle cx="8" cy="8" r="6.5" fill="none" stroke="var(--green)" stroke-width="1.5"/><path d="M1.5 8h13M8 1.5c-3 3.5-3 9.5 0 13M8 1.5c3 3.5 3 9.5 0 13" fill="none" stroke="var(--green)" stroke-width="1.1"/></svg>www.<span class="accent">varkelt</span>.co.uk</li>
      </ul>
    </div>
  </section>
</body>
</html>
```